Lumavento business card

We need a modern business card - With our 4 colors - See web: www.lumavento.dk

I have attached logo and som old business Cards we have - Lets Make the new ones shine...:-) -

Industry/Entity Type

Business

Requirements
Must have
• the logo with lumavento only,

```html
<!DOCTYPE html>
<html lang="da">
<head>
<meta charset="utf-8">
<title>Lumavento – visitkort</title>
<link rel="stylesheet" href="https://fonts.googleapis.com/css2?family=Source+Sans+3:wght@400;600&display=swap">
<style>
  :root {
    --lime: #8bc45a;
    --ink: #1d1d1b;
    --text: #4a4a4a;
    --paper: #ffffff;
    --backdrop: #ececec;
  }
  * { margin: 0; padding: 0; box-sizing: border-box; }
  html, body { width: 1105px; height: 1200px; overflow: hidden; }
  body {
    background: var(--backdrop);
    font-family: "Source Sans 3", sans-serif;
    position: relative;
  }
  .card {
    position: absolute;
    left: 192px;
    width: 720px;
    height: 412px;
    overflow: hidden;
  }
  .card--front { top: 146px; background: var(--paper); }
  .card--back { top: 602px; background: var(--lime); }

  .corner-art { position: absolute; inset: 0; width: 720px; height: 412px; }

  .person { position: absolute; left: 35px; top: 134px; }
  .person__name { color: var(--lime); font-size: 27px; font-weight: 600; line-height: 1.1; }
  .person__role { color: var(--ink); font-size: 18px; line-height: 1.3; }

  .contact { position: absolute; left: 37px; top: 218px; color: var(--text); font-size: 19px; line-height: 27.6px; list-style: none; }
  .contact li { display: flex; align-items: center; }
  .contact__icon { width: 16px; height: 16px; margin-right: 14px; flex: none; }

  .brand { position: absolute; display: flex; flex-direction: column; align-items: center; }
  .brand__row { display: flex; align-items: center; gap: 10px; }
  .brand__dot { width: 14px; height: 14px; border-radius: 50%; flex: none; }
  .brand__name { font-size: 26px; font-weight: 600; line-height: 1; }
  .brand__tagline { font-size: 15px; margin-top: 10px; }

  .card--front .brand { left: 440px; top: 150px; width: 244px; }
  .card--front .brand__dot { background: var(--lime); }
  .card--front .brand__name { color: var(--ink); }
  .card--front .brand__tagline { color: var(--text); }

  .card--back .brand { left: 392px; top: 300px; width: 304px; }
  .card--back .brand__dot { background: var(--paper); }
  .card--back .brand__name { color: var(--paper); }
  .card--back .brand__tagline { color: var(--paper); }
</style>
</head>
<body>

<section class="card card--front" aria-label="Visitkort forside">
  <svg class="corner-art" viewBox="0 0 720 412" aria-hidden="true">
    <path d="M0,0 H160 Q30,22 0,140 Z" fill="var(--lime)"/>
    <path d="M160,0 Q30,22 0,140 L0,150 Q40,30 172,0 Z" fill="var(--ink)"/>
    <path d="M720,412 V245 Q702,382 552,412 Z" fill="var(--lime)"/>
    <path d="M720,232 Q706,388 540,412 H552 Q702,382 720,245 Z" fill="var(--ink)"/>
  </svg>

  <div class="person">
    <h1 class="person__name">Malte Søgaard</h1>
    <p class="person__role">Salgsdirektør</p>
  </div>

  <ul class="contact">
    <li>Kastanievej 14</li>
    <li>2500 Valby</li>
    <li>
      <svg class="contact__icon" viewBox="0 0 16 16" aria-hidden="true"><path d="M3.5 1.5l2.5 3-1.5 1.8c.8 1.8 2.2 3.2 4 4l1.8-1.5 3 2.5-1.5 2.5C7 13.5 2.5 9 1 3z" fill="var(--lime)"/></svg>
      +45 31 42 67 80
    </li>
    <li>
      <svg class="contact__icon" viewBox="0 0 16 16" aria-hidden="true"><path d="M3.5 1.5l2.5 3-1.5 1.8c.8 1.8 2.2 3.2 4 4l1.8-1.5 3 2.5-1.5 2.5C7 13.5 2.5 9 1 3z" fill="var(--lime)"/></svg>
      +45 52 18 39 64
    </li>
    <li>
      <svg class="contact__icon" viewBox="0 0 16 16" aria-hidden="true"><rect x="1" y="3.5" width="14" height="9.5" fill="var(--lime)"/><path d="M1 3.5l7 5.5 7-5.5" fill="none" stroke="var(--paper)" stroke-width="1.3"/></svg>
      ms@lumavento.dk
    </li>
    <li>
      <svg class="contact__icon" viewBox="0 0 16 16" aria-hidden="true"><circle cx="8" cy="8" r="7" fill="var(--lime)"/><path d="M1 8h14M8 1c-3 3.5-3 10.5 0 14M8 1c3 3.5 3 10.5 0 14" fill="none" stroke="var(--paper)" stroke-width="1"/></svg>
      www.lumavento.dk
    </li>
  </ul>

  <div class="brand">
    <div class="brand__row">
      <span class="brand__dot"></span>
      <p class="brand__name">Lumavento</p>
    </div>
    <p class="brand__tagline">ungdomsmedier i Danmark</p>
  </div>
</section>

<section class="card card--back" aria-label="Visitkort bagside">
  <div class="brand">
    <div class="brand__row">
      <span class="brand__dot"></span>
      <p class="brand__name">Lumavento</p>
    </div>
    <p class="brand__tagline">ungdomsmedier i Danmark</p>
  </div>
</section>

</body>
</html>
```